Stylish Business Cards Wanted

- DOUBLE SIDED Design Required -

High end, edgy cards for a corporate and personal stylist. Must include logo,
Name: Belinda Harwick
Title: Director and Stylist
telephone : +61 8 7142 5809
email: belinda@theloombriefing.example
website: theloombriefing.example
Tag: Corporate Workwear & Uniform Specialist | Personal Stylist
Would like nice icons for telephone, email, website

Target Market(s)

Businesses wanting stylish uniforms, people wanting stylish wardrobes

Industry/Entity Type

Corporate Workwear Stylist

Contact Information for Business Card

I would like black, white and gold foiling incorporated in the design - possibly a touch of the other colours on my branding guide attached Name: Belinda Harwick Title: Director and Stylist telephone : +61 8 7142 5809 email: belinda@theloombriefing.example website: theloombriefing.example Tag: Corporate Workwear & Uniform Specialist | Personal Stylist Would like nice icons for telephone, email, website

Font styles to use
Other font styles liked:
• Raleway

Colors

Designer to choose colors to be used in the design.

Requirements
Must have
• Gold foil accents

```html
<!DOCTYPE html>
<html lang="en">
<head>
<meta charset="utf-8">
<title>The Loom Briefing – Business Cards</title>
<link rel="stylesheet" href="https://fonts.googleapis.com/css2?family=Raleway:wght@400;500;600&display=swap">
<style>
  :root {
    --bg: #2c2c2d;
    --card: #1f1f20;
    --edge: #a3165f;
    --gold: #d9b54a;
    --white: #ffffff;
    --muted: #c9c9c9;
  }
  * { margin: 0; padding: 0; box-sizing: border-box; }
  html, body { width: 1200px; height: 868px; overflow: hidden; }
  body {
    background: var(--bg);
    font-family: "Raleway", Arial, sans-serif;
    position: relative;
  }
  .card {
    position: absolute;
    background: var(--card);
    border-bottom: 6px solid var(--edge);
    border-right: 6px solid var(--edge);
    box-shadow: 0 18px 40px rgba(0,0,0,.45);
  }
  /* Contact side (portrait) */
  .card--back {
    left: 170px; top: 170px;
    width: 300px; height: 525px;
    display: flex; flex-direction: column; align-items: center; justify-content: center;
    text-align: center;
  }
  .holder-name {
    color: var(--gold);
    font-weight: 600;
    font-size: 19px;
    letter-spacing: 1px;
    text-transform: uppercase;
  }
  .holder-title {
    color: var(--white);
    font-size: 12px;
    margin-top: 4px;
  }
  .gold-rule {
    width: 34px; height: 2px;
    background: var(--gold);
    margin: 20px 0;
  }
  .contact-list { list-style: none; }
  .contact-list li {
    color: var(--white);
    font-size: 11.5px;
    display: flex; align-items: center; justify-content: center; gap: 6px;
    line-height: 1.7;
  }
  .contact-list svg { width: 11px; height: 11px; flex: none; }
  .services { list-style: none; }
  .services li {
    color: var(--muted);
    font-size: 11px;
    letter-spacing: 1.2px;
    text-transform: uppercase;
    line-height: 1.45;
  }
  /* Brand side (landscape) */
  .card--front {
    left: 540px; top: 260px;
    width: 525px; height: 300px;
    display: flex; align-items: center; justify-content: center;
  }
  .brand { display: flex; align-items: center; gap: 12px; }
  .brand-mark { width: 14px; height: 14px; background: var(--gold); }
  .brand-name {
    color: var(--white);
    font-weight: 500;
    font-size: 30px;
    letter-spacing: 2px;
    text-transform: uppercase;
  }
</style>
</head>
<body>
  <section class="card card--back" aria-label="Business card contact side">
    <h1 class="holder-name">Belinda Harwick</h1>
    <p class="holder-title">Director &amp; Stylist</p>
    <div class="gold-rule"></div>
    <ul class="contact-list">
      <li>
        <svg viewBox="0 0 12 12" fill="none" stroke="#d9b54a" stroke-width="1.1" aria-hidden="true"><path d="M2.5 1.5h2l1 2.5-1.3.9a6 6 0 0 0 2.9 2.9l.9-1.3 2.5 1v2a1 1 0 0 1-1 1A8.5 8.5 0 0 1 1.5 2.5a1 1 0 0 1 1-1z"/></svg>
        +61 8 7142 5809
      </li>
      <li>
        <svg viewBox="0 0 12 12" fill="none" stroke="#d9b54a" stroke-width="1.1" aria-hidden="true"><rect x="1" y="2.5" width="10" height="7"/><path d="M1 2.5l5 4 5-4"/></svg>
        belinda@theloombriefing.example
      </li>
      <li>
        <svg viewBox="0 0 12 12" fill="none" stroke="#d9b54a" stroke-width="1.1" aria-hidden="true"><circle cx="6" cy="6" r="5"/><ellipse cx="6" cy="6" rx="2.2" ry="5"/><path d="M1 6h10"/></svg>
        theloombriefing.example
      </li>
    </ul>
    <div class="gold-rule"></div>
    <ul class="services">
      <li>Corporate Workwear</li>
      <li>Uniform Specialist</li>
      <li>Personal Stylist</li>
    </ul>
  </section>

  <section class="card card--front" aria-label="Business card brand side">
    <div class="brand">
      <span class="brand-mark" aria-hidden="true"></span>
      <span class="brand-name">The Loom Briefing</span>
    </div>
  </section>
</body>
</html>
```